Looking for a modern, Professional business card design

We have a simple business card, but are looking for a more modern, professional look. A sample of the basic card is attached as well as the logo. We would also like to add that we offer:
Struggling with your finances?
- Learn to become debt free
- Discover the power of cash
- Control your money instead of it controlling you
Let us help you achieve a new level of financial freedom!
Also, we would like to have a "SPECIAL OFFER!: FREE 30 minute consultation"
Financial Planning

```html
<!DOCTYPE html>
<html lang="en">
<head>
<meta charset="UTF-8">
<title>Steadypath Money Coaching – Business Card</title>
<link href="https://fonts.googleapis.com/css2?family=Open+Sans:ital,wght@0,400;0,600;0,700;0,800;1,400&display=swap" rel="stylesheet">
<style>
  :root {
    --page-bg: #e9e6e1;
    --green-dark: #2f8a2c;
    --green-mid: #56ad35;
    --green-light: #b9dc4a;
    --green-text: #5aa83a;
    --ink: #1e1e1e;
    --grey-text: #3a3a3a;
    --white: #ffffff;
    --card-white: #fbfbfb;
    --black-band: #0d0d0d;
  }
  * { box-sizing: border-box; margin: 0; padding: 0; }
  html, body { width: 1200px; height: 843px; overflow: hidden; }
  body {
    background: var(--page-bg);
    font-family: "Open Sans", Arial, sans-serif;
    display: flex;
    align-items: center;
    justify-content: center;
    gap: 40px;
  }
  .card {
    position: relative;
    width: 540px;
    height: 309px;
    border-radius: 22px;
    overflow: hidden;
    box-shadow: 0 6px 18px rgba(0,0,0,0.18);
  }

  /* Back card */
  .card-back {
    background:
      radial-gradient(ellipse 60% 80% at 68% 45%, var(--green-light) 0%, var(--green-mid) 45%, var(--green-dark) 100%);
    color: var(--white);
    padding: 30px 34px;
  }
  .card-back .headline { font-weight: 700; font-size: 15px; letter-spacing: 0.2px; }
  .card-back .benefits { list-style: none; margin-top: 4px; font-style: italic; font-size: 14px; line-height: 1.35; }
  .card-back .benefits li::before { content: "\2022"; font-style: normal; margin-right: 8px; }
  .card-back .invite { font-style: italic; font-size: 14px; margin-top: 6px; }
  .card-back .offer-title { font-weight: 800; font-size: 20px; margin-top: 12px; line-height: 1.1; }
  .card-back .offer-text { font-weight: 600; font-size: 13px; }
  .card-back .brand-name {
    position: absolute; left: 34px; bottom: 30px;
    font-weight: 800; font-size: 30px; letter-spacing: 1px; text-transform: uppercase; line-height: 1;
  }

  /* Front card */
  .card-front {
    background: linear-gradient(160deg, var(--white) 0%, var(--card-white) 60%, #ececec 100%);
  }
  .brand-lockup {
    position: absolute; top: 52px; right: 34px;
    display: flex; align-items: center; gap: 10px;
  }
  .brand-lockup .dot { width: 34px; height: 34px; border-radius: 50%; background: var(--green-mid); }
  .brand-lockup .brand-name {
    font-weight: 800; font-size: 22px; color: var(--ink); text-transform: uppercase; line-height: 1.05;
  }
  .contact { position: absolute; left: 42px; top: 70px; color: var(--grey-text); }
  .contact .person { color: var(--green-text); font-size: 21px; font-weight: 400; }
  .contact .role { font-size: 16px; color: var(--ink); margin-bottom: 6px; }
  .contact .line { display: flex; align-items: center; gap: 10px; font-size: 15px; line-height: 1.5; }
  .contact .line svg { width: 14px; height: 14px; }
  .band { position: absolute; left: 0; bottom: 0; width: 540px; height: 130px; }
  .website { font-family: "Open Sans", Arial, sans-serif; font-size: 14px; fill: var(--white); }
</style>
</head>
<body>

  <section class="card card-back" aria-label="Card back">
    <p class="headline">STRUGGLING WITH YOUR FINANCES?</p>
    <ul class="benefits">
      <li>Learn to become debt free</li>
      <li>Discover the power of cash</li>
      <li>Control your money instead of it controlling you</li>
    </ul>
    <p class="invite">Let us help you achieve a new level of financial freedom!</p>
    <p class="offer-title">SPECIAL OFFER!</p>
    <p class="offer-text">FREE 30 minute consultation</p>
    <p class="brand-name">Steadypath</p>
  </section>

  <section class="card card-front" aria-label="Card front">
    <div class="brand-lockup">
      <span class="dot"></span>
      <span class="brand-name">Steadypath<br>Money Coaching</span>
    </div>

    <div class="contact">
      <p class="person">Daniel R. Hayes</p>
      <p class="role">Personal Financial Coach</p>
      <p class="line">
        <svg viewBox="0 0 14 14" aria-hidden="true"><rect x="3" y="0.5" width="8" height="13" rx="1.5" fill="none" stroke="var(--green-mid)" stroke-width="1.4"/><circle cx="7" cy="11" r="0.9" fill="var(--green-mid)"/></svg>
        (555) 014-2387
      </p>
      <p class="line">
        <svg viewBox="0 0 14 14" aria-hidden="true"><rect x="0.5" y="2.5" width="13" height="9" rx="1" fill="var(--green-mid)"/><path d="M1 3 L7 8 L13 3" fill="none" stroke="#fff" stroke-width="1.2"/></svg>
        daniel@steadypathmoney.com
      </p>
    </div>

    <svg class="band" viewBox="0 0 540 130" aria-label="Website">
      <defs>
        <linearGradient id="bandGreen" x1="0" y1="0" x2="1" y2="0">
          <stop offset="0" stop-color="#3f9a2f"/>
          <stop offset="0.6" stop-color="#7fc23c"/>
          <stop offset="1" stop-color="#c4e27a"/>
        </linearGradient>
      </defs>
      <path d="M0 10 L540 58 L540 86 L0 46 Z" fill="url(#bandGreen)"/>
      <path d="M0 46 L540 86 L540 130 L0 130 Z" fill="#f4f4f4"/>
      <path d="M420 77 L540 86 L540 130 L470 130 Z" fill="var(--black-band)"/>
      <circle cx="448" cy="97" r="11" fill="var(--green-mid)"/>
      <text class="website" x="34" y="38" transform="rotate(5.08 34 38)">www.steadypathmoney.com</text>
    </svg>
  </section>

</body>
</html>
```